Shipping and Logistics, Project

Project description : Company Profile

A total logistics company covering domestic / international freight forwarding, warehouse management services, haulage, supply chain management, transport management & distribution, procurement & assembly services, shipping, chartering & bunker services, project logistics & tax exemption consultancy, oil & gas logistics, halal logistics services & integrated logistics management. We’re a well-established and experienced freight forwarder in Kuala Lumpur, Malaysia. We specialize in customized value-added solution that optimizes your supply chain by trimming inventory, reducing logistics cost and enhancing your customer service levels.

As a member of the Worldwide Parcel and Carriage Alliance which comprise of 170 global freight agents in 80 countries that promotes great handling in cross-trade logistics and freighting. You could rely on our efficiency in handlings of export cargo (FCL, LCL, Bulk and Conventional) between our global network offices worldwide with a total scale of 10,000 groomed specialists in various logistics division working together to ensure delivery task meets with your expectation. With our dedicated qualified and experienced professionals, we are fully committed to serving our clients.

Our generic services are listed below for your reference:

• Air Freight
• Ocean Freight FCL & LCL
• Container Haulage
• Warehousing
• Transportation and Distribution within Malaysia and Thailand
• Cross-Border Road Line-hauls between Thailand, Malaysia, Singapore and Laos
• Customs Brokerage and Forwarding
• Project Cargo Freight Forwarding for setting up of new plants / factories and ad hoc heavy-lift
• Air-Sea-Road-Rail multi-modal options
• Import / Export / Storage / Documentation / Handling of DG / Hazmat
• Vessel and Aircraft Charters

Our Mission
Based on the motto “Quick, Reliable and Polite”, we are dedicated to upholding the following three points corporate philosophy:
1. Adhering to the principle that “the customer always comes first”.
2. Contributing to the development of the local community.
3. Making it our duty to be responsible and sincere.

Our Edge
• One-Stop Logistics Solutions
• Extensive Network Throughout Malaysia
• Highly Qualified and Experienced Pool of Professionals
• Comprehensive IT Solutions
• Innovative and Customer-focused Solutions
• Flexible and Consistent in Managing Exceptions
• Total Supply Chain Visibility

Target Market
1. We sell the logistics services to all the industry in Malaysia and Worldwide. (ONE Stop Logistics Solutions)

Competitor
1. TR Valmont
2. Corvessa Transport
3. Brandt + Loewe
4. FELRO
5. QTV
6. Routemarks
7. Ilto Logistics

Rules for Picking a Company Name
1. Unique and unforgettable
2. Avoid unusual spellings
3. Easy to pronounce and remember
4. Keep it simple
5. Make some sense
6. Give a clue

Rules for Picking a Company Logo
4. Keep it simple
5. Make some sense
6. Give a clue

1. Simplicity
2. Memorability
3. Originality
4. Modern Yet Timeless
5. Balance
6. Complementary
7. Versatility

Stationery Information
1. Company Name : ZENFreight Solutions Sdn Bhd
2. Company Registration : 2837165-W
3. Address : 42-08, Jalan Cempaka Indah 5, Taman Seri Bayu, 81300 Johor Bahru, Johor, Malaysia.
4. Name : Derek Tan
5. Position : Manager
6. Mobile No : (+6019) 4381907
7. Office No : (+607) 5218764
8. Fax No : Not Available
9. Email Address : derek.tan@zenfreight-solutions.example
10. Web Domain : www.zenfreight-solutions.example
11. Company Slogan : Be Globally Connected

Target Market(s)

Corporate Company

Industry/Entity Type

Shipping and Logistics Industry

Requirements
Must have
• Company Full Name : ZENFREIGHT SOLUTIONS SDN. BHD.
Nice to have
• Keep it simple and unforgettable ...

```html
<!DOCTYPE html>
<html lang="en">
<head>
<meta charset="utf-8">
<title>ZENFreight Solutions – Stationery Set</title>
<link rel="stylesheet" href="https://fonts.googleapis.com/css2?family=Poppins:wght@400;500;600&display=swap">
<style>
  :root {
    --backdrop: #c8c8c8;
    --brand-blue: #3c87c8;
    --charcoal: #272727;
    --paper: #ffffff;
    --ink: #1e1e1e;
    --mist: #e8f0f8;
    --mist-soft: #f5f7f9;
  }
  * { margin: 0; padding: 0; box-sizing: border-box; }
  html, body {
    width: 1200px; height: 900px; overflow: hidden;
    background: var(--backdrop);
    font-family: "Poppins", sans-serif;
  }
  .stationery-set { position: relative; width: 1200px; height: 900px; }
  .piece { position: absolute; overflow: hidden; }
  .piece svg.backdrop-shape { position: absolute; inset: 0; width: 100%; height: 100%; }

  /* Wordmark */
  .wordmark { position: absolute; display: flex; align-items: center; }
  .wordmark-square { border: 2px solid var(--brand-blue); flex: none; }
  .wordmark-text { display: flex; flex-direction: column; }
  .wordmark-name { font-weight: 500; color: var(--brand-blue); line-height: 1; }
  .wordmark-sub { font-weight: 600; color: var(--ink); letter-spacing: .12em; line-height: 1; }

  /* Presentation folder */
  .folder { left: 114px; top: 145px; width: 314px; height: 435px; background: var(--charcoal); }
  .folder .wordmark { left: 62px; top: 20px; }
  .folder .wordmark-square { width: 44px; height: 44px; margin-right: 10px; border-width: 3px; }
  .folder .wordmark-name { font-size: 24px; }
  .folder .wordmark-sub { font-size: 8.5px; color: var(--paper); margin-top: 6px; }
  .folder-slogan {
    position: absolute; left: 0; right: 0; top: 400px; text-align: center;
    font-size: 8.5px; letter-spacing: .18em; color: #c9d7e4;
  }

  /* Letterhead */
  .letterhead { left: 460px; top: 154px; width: 291px; height: 425px; background: var(--paper); }
  .letterhead .wordmark { left: 24px; top: 10px; }
  .letterhead .wordmark-square { width: 24px; height: 24px; margin-right: 8px; }
  .letterhead .wordmark-name { font-size: 12px; }
  .letterhead .wordmark-sub { font-size: 4.3px; margin-top: 3px; }
  .letterhead-contact {
    position: absolute; right: 18px; top: 16px; text-align: right;
    font-size: 5px; line-height: 6.2px; color: var(--ink);
  }
  .letterhead-contact .accent { color: var(--brand-blue); }
  .letterhead-band {
    position: absolute; left: 0; right: 0; top: 43px; height: 12px;
    background: var(--brand-blue); color: var(--paper);
    font-size: 5.6px; display: flex; justify-content: space-between; align-items: center;
    padding: 0 18px 0 37px;
  }
  .letterhead-footer {
    position: absolute; left: 0; right: 0; bottom: 0; height: 15px;
    background: var(--charcoal); color: var(--paper);
    font-size: 4.8px; display: flex; justify-content: center; align-items: center;
  }

  /* Large envelope */
  .envelope-large { left: 786px; top: 94px; width: 307px; height: 488px; }
  .envelope-large .wordmark { left: 25px; top: 95px; }
  .envelope-large .wordmark-square { width: 24px; height: 24px; margin-right: 6px; }
  .envelope-large .wordmark-name { font-size: 11px; }
  .envelope-large .wordmark-sub { font-size: 4px; margin-top: 3px; }
  .envelope-large-address {
    position: absolute; left: 0; right: 0; top: 470px; text-align: center;
    font-size: 4.8px; color: var(--ink);
  }

  /* DL envelope */
  .envelope-dl { left: 436px; top: 624px; width: 340px; height: 196px; }
  .envelope-dl .wordmark { left: 17px; top: 49px; }
  .envelope-dl .wordmark-square { width: 22px; height: 22px; margin-right: 5px; }
  .envelope-dl .wordmark-name { font-size: 9.5px; }
  .envelope-dl .wordmark-sub { font-size: 3.6px; margin-top: 2px; }
  .envelope-dl-address {
    position: absolute; left: 19px; top: 163px;
    font-size: 5.2px; line-height: 6.5px; color: var(--ink);
  }
</style>
</head>
<body>
<main class="stationery-set">

  <!-- Presentation folder -->
  <section class="piece folder" aria-label="Presentation folder">
    <svg class="backdrop-shape" viewBox="0 0 314 435" preserveAspectRatio="none" aria-hidden="true">
      <polygon fill="var(--brand-blue)" points="0,435 0,415 33,392 107,351 110,312 142,325 201,290 197,244 240,265 283,236 283,202 314,216 314,435"/>
    </svg>
    <div class="wordmark">
      <span class="wordmark-square"></span>
      <span class="wordmark-text">
        <span class="wordmark-name">ZENFREIGHT</span>
        <span class="wordmark-sub">SOLUTIONS SDN. BHD.</span>
      </span>
    </div>
    <p class="folder-slogan">BE GLOBALLY CONNECTED</p>
  </section>

  <!-- Letterhead -->
  <section class="piece letterhead" aria-label="Letterhead">
    <svg class="backdrop-shape" viewBox="0 0 291 425" preserveAspectRatio="none" aria-hidden="true">
      <polygon fill="var(--mist)" points="115,410 115,355 150,375 198,347 193,300 230,318 266,294 266,287 291,300 291,410"/>
    </svg>
    <div class="wordmark">
      <span class="wordmark-square"></span>
      <span class="wordmark-text">
        <span class="wordmark-name">ZENFREIGHT</span>
        <span class="wordmark-sub">SOLUTIONS SDN. BHD.</span>
      </span>
    </div>
    <address class="letterhead-contact" style="font-style:normal">
      (+6019) 438 1907, (+607) 521 8764<br>
      derek.tan@zenfreight-solutions.example<br>
      www.<span class="accent">zenfreight-solutions</span>.example
    </address>
    <div class="letterhead-band">
      <span>BE GLOBALLY CONNECTED</span>
      <span>Company No. 2837165-W</span>
    </div>
    <div class="letterhead-footer">42-08, Jalan Cempaka Indah 5, Taman Seri Bayu, 81300 Johor Bahru, Johor, Malaysia.</div>
  </section>

  <!-- Large envelope -->
  <section class="piece envelope-large" aria-label="Large envelope">
    <svg class="backdrop-shape" viewBox="0 0 307 488" preserveAspectRatio="none" aria-hidden="true">
      <polygon fill="var(--paper)" points="0,57 307,60 307,488 0,488"/>
      <polygon fill="var(--brand-blue)" points="33,0 270,0 307,52 307,60 0,57 0,51"/>
      <polygon fill="var(--mist)" points="55,488 55,440 112,400 200,365 216,300 252,325 290,300 307,290 307,488"/>
    </svg>
    <div class="wordmark">
      <span class="wordmark-square"></span>
      <span class="wordmark-text">
        <span class="wordmark-name">ZENFREIGHT</span>
        <span class="wordmark-sub">SOLUTIONS SDN. BHD.</span>
      </span>
    </div>
    <p class="envelope-large-address">42-08, Jalan Cempaka Indah 5, Taman Seri Bayu, 81300 Johor Bahru, Johor, Malaysia.</p>
  </section>

  <!-- DL envelope -->
  <section class="piece envelope-dl" aria-label="DL envelope">
    <svg class="backdrop-shape" viewBox="0 0 340 196" preserveAspectRatio="none" aria-hidden="true">
      <rect fill="var(--paper)" x="0" y="26" width="340" height="170"/>
      <polygon fill="var(--brand-blue)" points="15,0 323,0 340,26 0,26"/>
      <polygon fill="var(--mist-soft)" points="250,196 270,180 305,160 312,135 340,120 340,196"/>
    </svg>
    <div class="wordmark">
      <span class="wordmark-square"></span>
      <span class="wordmark-text">
        <span class="wordmark-name">ZENFREIGHT</span>
        <span class="wordmark-sub">SOLUTIONS SDN. BHD.</span>
      </span>
    </div>
    <address class="envelope-dl-address" style="font-style:normal">
      42-08, Jalan Cempaka Indah 5,<br>
      Taman Seri Bayu, 81300 Johor<br>
      Bahru, Johor, Malaysia.
    </address>
  </section>

</main>
</body>
</html>
```